Create a memorable Web Design for real estate branding

we are a Minnepolis brokerage and boutique housing specialist with over 27 years of experience in the Global furnished housing industry, servicing the Greater Los Angeles area. Specializing in “warm environments” we offer a customized approach to satisfying our guests and client’s needs by offering a wide array of options in highly desirable areas. Additionally, Lantern Dwelling Partners offers assistance and expertise to home buyers, sellers and investors.

Industry/Entity Type

Real Estate

Number of Pages Required

1 page

Font styles to use
Serif
Sans Serif
Decorative

```html
<!DOCTYPE html>
<html lang="en">
<head>
<meta charset="utf-8">
<title>Lantern Dwelling Partners</title>
<link href="https://fonts.googleapis.com/css2?family=Open+Sans:ital,wght@0,400;0,600;0,700;1,400&family=Cinzel:wght@400;600&family=Libre+Baskerville:ital@1&display=swap" rel="stylesheet">
<style>
:root{
  --green:#7dc52e;
  --green-dark:#6cb324;
  --teal:#1a9f85;
  --ink:#333;
  --muted:#666;
  --line:#dcdcdc;
  --footer:#2b2b2b;
  --white:#fff;
}
*{margin:0;padding:0;box-sizing:border-box}
html,body{width:1200px;height:3136px;overflow:hidden}
body{position:relative;font-family:"Open Sans",Arial,sans-serif;color:var(--ink);background:var(--white)}
.abs{position:absolute}

/* nav */
.site-nav{left:0;top:0;width:1200px;height:88px;background:var(--white);border-top:3px solid var(--teal);box-shadow:0 2px 4px rgba(0,0,0,.12);z-index:2}
.brand{left:84px;top:20px;font-family:"Cinzel",serif;font-weight:600;font-size:25px;color:var(--teal);line-height:1.05;width:300px}
.menu{right:48px;top:0;display:flex;height:85px}
.menu a{display:flex;align-items:center;padding:0 26px;font-size:13px;color:#444;text-decoration:none;text-transform:uppercase}
.menu a.active{background:var(--teal);color:var(--white)}

/* hero */
.hero{left:0;top:88px;width:1200px;height:497px;background:linear-gradient(135deg,#e9e2d6 0%,#b99a78 35%,#6d4a32 65%,#8a9b7c 85%,#556b4b 100%)}
.hero-arrow{top:310px;width:54px;height:54px;border:2px solid var(--white);border-radius:50%;background:rgba(0,0,0,.35);display:flex;align-items:center;justify-content:center}
.hero-title{right:86px;top:432px;text-align:right;color:var(--white);font-weight:700;font-size:30px;line-height:44px;text-shadow:0 2px 4px rgba(0,0,0,.5)}

/* search */
.search{left:84px;top:580px;width:1030px;height:141px;background:var(--white);border-top:5px solid var(--green);box-shadow:0 2px 6px rgba(0,0,0,.15);z-index:2}
.field{position:absolute;height:34px;border:1px solid #ccc;font-size:12px;color:#666;display:flex;align-items:center;padding-left:12px}
.field.select::after{content:"";position:absolute;right:12px;top:14px;border:4px solid transparent;border-top:5px solid #444}
.btn-search{position:absolute;height:36px;background:var(--teal);color:var(--white);font-weight:600;font-size:13px;display:flex;align-items:center;justify-content:center}

/* welcome */
.welcome{left:0;top:721px;width:1200px;height:498px;background:linear-gradient(90deg,#f3f4f5,#e9ebec 60%,#f1f2f3)}
.welcome-photo{left:98px;top:52px;width:295px;height:404px;background:linear-gradient(180deg,#5d7ea6 0%,#7c5443 45%,#4b3326 75%,#6d6b60 100%)}
.welcome-photo::after{content:"";position:absolute;inset:10px;border:2px solid rgba(255,255,255,.85)}
.welcome-kicker{left:441px;top:60px;color:var(--green);font-weight:700;font-size:20px}
.welcome-title{left:441px;top:86px;color:var(--teal);font-family:"Cinzel",serif;font-size:30px;letter-spacing:1px}
.welcome-text{left:441px;width:670px;font-size:12.5px;line-height:25px;color:#777}
.room{top:355px;width:160px;text-align:center}
.room svg{display:block;margin:0 auto}
.room-label{font-size:13px;font-weight:700;color:#333;margin-top:6px}
.room-num{font-family:"Libre Baskerville",serif;font-style:italic;font-size:34px;color:#333;line-height:44px}

/* section headings */
.section-title{left:0;width:1200px;text-align:center;font-weight:700;font-size:24px}
.section-title .a{color:var(--green)}
.section-title .b{color:var(--teal)}
.section-lead{left:220px;width:760px;text-align:center;font-size:12.5px;line-height:26px;color:#555}

/* featured */
.card{top:1373px;width:327px;height:450px;border:1px solid var(--line);background:var(--white)}
.card-photo{height:220px}
.card-specs{display:flex;gap:20px;padding:14px 16px;font-size:12px;color:#555;border-bottom:1px solid #eee}
.card-specs span{display:flex;align-items:center;gap:5px}
.card-title{padding:18px 16px 6px;font-weight:700;font-size:15px;color:#333}
.card-text{padding:0 16px;font-size:12.5px;line-height:26px;color:#666;height:80px}
.card-foot{position:absolute;left:0;right:0;bottom:0;height:52px;border-top:1px solid #eee;display:flex;align-items:center;justify-content:space-between;padding:0 16px}
.card-addr{font-size:12px;color:#777;display:flex;gap:5px;align-items:center}
.card-price{font-size:19px;font-weight:700;color:var(--green)}

/* agents */
.agents{left:0;top:1860px;width:1200px;height:324px;background:linear-gradient(135deg,#86cf33 0%,#72bb26 50%,#84cc30 100%)}
.agents-title{top:42px;left:0;width:1200px;text-align:center;color:var(--white);font-weight:700;font-size:24px}
.agents-quote{left:230px;top:94px;width:740px;text-align:center;color:var(--white);font-style:italic;font-size:12.5px;line-height:25px}
.quote-mark{color:var(--white);font-family:Georgia,serif;font-size:44px;font-weight:700;line-height:1}
.avatar{border-radius:50%;border:3px solid var(--white)}
.chev{top:192px}
.agent-name{top:268px;left:0;width:1200px;text-align:center;color:var(--white);font-style:italic;font-size:13px}
.agent-social{top:297px;left:582px;display:flex;gap:8px}
.agent-social i{width:8px;height:8px;border-radius:50%;background:var(--white);display:block}

/* gallery */
.filters{left:251px;top:2326px;width:696px;height:50px;border:1px solid var(--line);display:flex;align-items:center;justify-content:center;gap:16px;font-size:12px;color:#555;text-transform:uppercase}
.filters .on{color:var(--green)}
.filters .sep{color:#999}
.gallery-main{left:84px;top:2401px;width:681px;height:368px;background:linear-gradient(180deg,#3b4f7a 0%,#6a6f86 45%,#8a6a4a 70%,#2f7f8f 100%)}
.gallery-side{left:780px;width:334px}
.gal-arrow{top:2560px;width:48px;height:48px;border:2px solid var(--white);border-radius:50%;background:rgba(0,0,0,.35);display:flex;align-items:center;justify-content:center}

/* footer */
.footer{left:0;top:2815px;width:1200px;height:251px;background:var(--footer);color:#ddd}
.footer-brand{left:84px;top:100px;font-family:"Cinzel",serif;font-weight:600;font-size:26px;color:var(--white);width:300px;line-height:1.15}
.footer-col{top:55px}
.footer-col h3{font-weight:400;font-size:17px;color:var(--white);margin-bottom:24px;text-transform:uppercase;letter-spacing:.5px}
.contact-line{display:flex;gap:14px;font-size:11.5px;line-height:16px;margin-bottom:12px}
.contact-line svg{flex:none;margin-top:1px}
.email-input{width:208px;height:33px;background:var(--white);color:#555;font-size:12px;display:flex;align-items:center;padding-left:14px;margin-top:14px}
.btn-sub{margin-top:12px;width:80px;height:26px;background:var(--teal);color:var(--white);font-size:11px;display:flex;align-items:center;justify-content:center}
.social{display:flex;gap:8px;margin-top:16px}
.social i{width:36px;height:36px;border:2px solid var(--white);border-radius:50%;display:block}
.copyright{left:0;top:3066px;width:1200px;height:70px;background:var(--green);color:var(--white);font-size:12.5px;display:flex;align-items:center;justify-content:center}
</style>
</head>
<body>

<header class="site-nav abs">
  <div class="brand abs">Lantern Dwelling Partners</div>
  <nav class="menu abs">
    <a class="active">Home</a><a>About Us</a><a>Services</a><a>Property</a><a>Gallery</a><a>Contact Us</a>
  </nav>
</header>

<section class="hero abs" role="img" aria-label="Bright living room with cream sofas, fireplace and tall glass wall to a garden"></section>
<div class="hero-arrow abs" style="left:26px"><svg width="18" height="18" viewBox="0 0 18 18"><path d="M12 2 5 9l7 7" fill="none" stroke="#fff" stroke-width="2.5"/></svg></div>
<div class="hero-arrow abs" style="left:1120px"><svg width="18" height="18" viewBox="0 0 18 18"><path d="M6 2l7 7-7 7" fill="none" stroke="#fff" stroke-width="2.5"/></svg></div>
<div class="hero-title abs">SPECIALIZING IN<br>WARM ENVIRONMENTS</div>

<form class="search abs">
  <div class="field" style="left:56px;top:25px;width:606px">Search Keyword...</div>
  <div class="field select" style="left:689px;top:25px;width:130px">Location</div>
  <div class="btn-search" style="left:848px;top:24px;width:132px">SEARCH</div>
  <div class="field select" style="left:56px;top:73px;width:132px">Property Type</div>
  <div class="field select" style="left:217px;top:73px;width:130px">Select Status</div>
  <div class="field select" style="left:376px;top:73px;width:130px">Beds</div>
  <div class="field select" style="left:533px;top:73px;width:130px">Baths</div>
  <div class="field select" style="left:689px;top:73px;width:130px">$ Min Price</div>
  <div class="field select" style="left:848px;top:73px;width:132px">$ Max Price</div>
</form>

<section class="welcome abs">
  <div class="welcome-photo abs" role="img" aria-label="Brick two-storey house lit at dusk with a paved front patio"></div>
  <div class="welcome-kicker abs">WELCOME TO</div>
  <div class="welcome-title abs">LANTERN DWELLING PARTNERS</div>
  <p class="welcome-text abs" style="top:132px">Sed ut perspiciatis unde omnis iste natus error sit voluptatem accusantium doloremque laudantium, totam rem aperiam, eaque ipsa quae ab illo inventore veritatis et quasi architecto beatae vitae dicta sunt explicabo. Nemo enim ipsam voluptatem quia voluptas sit aspernatur aut odit aut fugit, sed quia consequuntur magni dolores eos porro quisquam est, qui dolorem ipsum quia dolor sit amet, consectetur, adipisci velit, sed</p>
  <p class="welcome-text abs" style="top:245px">Inventore veritatis et quasi architecto beatae vitae dicta sunt explicabo. Nemo enim ipsam voluptatem quia voluptas sit aspernatur aut odit aut fugit, sed quia consequuntur magni dolores eos porro quisquam est, qui dolorem ipsum quia dolor sit amet, consectetur, adipisci velit, sed</p>

  <div class="room abs" style="left:436px">
    <svg width="40" height="40" viewBox="0 0 40 40" fill="var(--green)"><rect x="6" y="8" width="3" height="26"/><path d="M9 8h10a6 6 0 0 1 6 6H9z"/><rect x="4" y="18" width="32" height="4" rx="2"/><rect x="7" y="22" width="26" height="8" rx="3"/></svg>
    <div class="room-label">BATHROOM</div><div class="room-num">03</div>
  </div>
  <div class="room abs" style="left:601px">
    <svg width="40" height="40" viewBox="0 0 40 40" fill="var(--green)"><rect x="5" y="8" width="30" height="12" rx="2"/><rect x="9" y="11" width="9" height="6" rx="1" fill="#eee"/><rect x="22" y="11" width="9" height="6" rx="1" fill="#eee"/><rect x="3" y="21" width="34" height="9" rx="1"/><rect x="4" y="30" width="3" height="4"/><rect x="33" y="30" width="3" height="4"/></svg>
    <div class="room-label">BEDROOM</div><div class="room-num">03</div>
  </div>
  <div class="room abs" style="left:766px">
    <svg width="40" height="40" viewBox="0 0 40 40" fill="var(--green)"><rect x="8" y="10" width="24" height="12" rx="3"/><rect x="3" y="16" width="7" height="14" rx="2"/><rect x="30" y="16" width="7" height="14" rx="2"/><rect x="9" y="22" width="22" height="8"/><rect x="5" y="30" width="3" height="4"/><rect x="32" y="30" width="3" height="4"/></svg>
    <div class="room-label">KIDSROOM</div><div class="room-num">01</div>
  </div>
  <div class="room abs" style="left:930px">
    <svg width="40" height="40" viewBox="0 0 40 40" fill="var(--green)"><rect x="6" y="9" width="28" height="8" rx="2"/><rect x="3" y="18" width="34" height="12" rx="2"/><rect x="3" y="22" width="34" height="2" fill="#eee"/><rect x="4" y="30" width="3" height="4"/><rect x="33" y="30" width="3" height="4"/></svg>
    <div class="room-label">GUESTROOM</div><div class="room-num">01</div>
  </div>
</section>

<h2 class="section-title abs" style="top:1252px"><span class="a">FEATURED</span> <span class="b">PROPERTYS</span></h2>
<p class="section-lead abs" style="top:1295px">Inventore veritatis et quasi architecto beatae vitae dicta sunt explicabo. Nemo enim ipsam voluptatem quia voluptas sit aspernatur qui dolorem ipsum quia dolor sit amet, consectetur, adipisci velit, sed</p>

<article class="card abs" style="left:84px">
  <div class="card-photo" role="img" aria-label="Hotel-style bedroom with dark headboard and orange accent panels" style="background:linear-gradient(135deg,#5a3a2a,#b5603a 40%,#e8dccb 70%,#6b4a36)"></div>
  <div class="card-specs"><span>⌂ 12,000 Sq Ft</span><span>▭ 3 Bedroom</span><span>◫ 2 Bathroom</span></div>
  <div class="card-title">CONTRARY TO POPULAR</div>
  <p class="card-text">Inventore veritatis et quasi architecto beatae vitae dicta sunt explicabo. Nemo enim ipsam voluptatem quia voluptas sit aspernatur...</p>
  <div class="card-foot"><span class="card-addr"><svg width="9" height="12" viewBox="0 0 9 12"><path d="M4.5 0A4.5 4.5 0 0 0 0 4.5C0 8 4.5 12 4.5 12S9 8 9 4.5A4.5 4.5 0 0 0 4.5 0z" fill="#888"/><circle cx="4.5" cy="4.5" r="1.6" fill="#fff"/></svg>12 1st Ave, Lorm ipsum dummy</span><span class="card-price">$154.00</span></div>
</article>
<article class="card abs" style="left:437px">
  <div class="card-photo" role="img" aria-label="Covered wooden deck with outdoor seating at dusk" style="background:linear-gradient(160deg,#3a4660,#6a5644 45%,#c69a62 65%,#4a3a2e)"></div>
  <div class="card-specs"><span>⌂ 12,000 Sq Ft</span><span>▭ 3 Bedroom</span><span>◫ 2 Bathroom</span></div>
  <div class="card-title">CONTRARY TO POPULAR</div>
  <p class="card-text">Inventore veritatis et quasi architecto beatae vitae dicta sunt explicabo. Nemo enim ipsam voluptatem quia voluptas sit aspernatur...</p>
  <div class="card-foot"><span class="card-addr"><svg width="9" height="12" viewBox="0 0 9 12"><path d="M4.5 0A4.5 4.5 0 0 0 0 4.5C0 8 4.5 12 4.5 12S9 8 9 4.5A4.5 4.5 0 0 0 4.5 0z" fill="#888"/><circle cx="4.5" cy="4.5" r="1.6" fill="#fff"/></svg>12 1st Ave, Lorm ipsum dummy</span><span class="card-price">$154.00</span></div>
</article>
<article class="card abs" style="left:788px">
  <div class="card-photo" role="img" aria-label="Warmly lit lounge with red seating under a timber roof" style="background:linear-gradient(170deg,#2e1f18,#7a4a2a 40%,#c07a3a 60%,#8a2a20 85%,#3a2418)"></div>
  <div class="card-specs"><span>⌂ 12,000 Sq Ft</span><span>▭ 3 Bedroom</span><span>◫ 2 Bathroom</span></div>
  <div class="card-title">CONTRARY TO POPULAR</div>
  <p class="card-text">Inventore veritatis et quasi architecto beatae vitae dicta sunt explicabo. Nemo enim ipsam voluptatem quia voluptas sit aspernatur...</p>
  <div class="card-foot"><span class="card-addr"><svg width="9" height="12" viewBox="0 0 9 12"><path d="M4.5 0A4.5 4.5 0 0 0 0 4.5C0 8 4.5 12 4.5 12S9 8 9 4.5A4.5 4.5 0 0 0 4.5 0z" fill="#888"/><circle cx="4.5" cy="4.5" r="1.6" fill="#fff"/></svg>12 1st Ave, Lorm ipsum dummy</span><span class="card-price">$154.00</span></div>
</article>

<section class="agents abs">
  <h2 class="agents-title abs">MEET OUR AGENTS</h2>
  <div class="quote-mark abs" style="left:196px;top:84px">“</div>
  <p class="agents-quote abs">Sed ut perspiciatis unde omnis iste natus error sit voluptatem accusantium doloremque laudantium, totam rem aperiam, eaque ipsa quae ab illo inventore veritatis et quasi architecto beatae vitae dicta sunt explicabo. Nemo enim ipsam voluptatem quia voluptas sit aspernatur aut odit aut fugit, sed quia consequuntur magni dolores eos qui</p>
  <div class="quote-mark abs" style="left:878px;top:154px">”</div>
  <svg class="chev abs" style="left:420px" width="16" height="50" viewBox="0 0 16 50"><path d="M14 2 2 25l12 23" fill="none" stroke="rgba(255,255,255,.8)" stroke-width="2"/></svg>
  <svg class="chev abs" style="left:764px" width="16" height="50" viewBox="0 0 16 50"><path d="M2 2l12 23L2 48" fill="none" stroke="rgba(255,255,255,.8)" stroke-width="2"/></svg>
  <div class="avatar abs" role="img" aria-label="Agent portrait" style="left:472px;top:188px;width:68px;height:68px;background:radial-gradient(circle,#c9a46a,#7a8a3a)"></div>
  <div class="avatar abs" role="img" aria-label="Featured agent portrait" style="left:554px;top:178px;width:88px;height:88px;background:radial-gradient(circle,#d8b08a,#5a6a7a)"></div>
  <div class="avatar abs" role="img" aria-label="Agent portrait" style="left:652px;top:188px;width:68px;height:68px;background:radial-gradient(circle,#d1a070,#8a6a3a)"></div>
  <div class="agent-name abs">Name : Theo Marsh</div>
  <div class="agent-social abs"><i></i><i></i><i></i></div>
</section>

<h2 class="section-title abs" style="top:2215px"><span class="a">PHOTO</span> <span class="b">GALLERY</span></h2>
<p class="section-lead abs" style="top:2255px">Inventore veritatis et quasi architecto beatae vitae dicta sunt explicabo. Nemo enim ipsam voluptatem quia voluptas sit aspernatur qui dolorem ipsum quia dolor sit amet, consectetur, adipisci velit, sed</p>
<div class="filters abs">
  <span class="on">All</span><span class="sep">|</span><span>Living Room</span><span class="sep">|</span><span>Driveway</span><span class="sep">|</span><span>Basement</span><span class="sep">|</span><span>Bedroom</span><span class="sep">|</span><span>Garage</span><span class="sep">|</span><span>Kitchen</span>
</div>
<div class="gallery-main abs" role="img" aria-label="Two-storey house at dusk with lit windows and a pool in front"></div>
<div class="gal-arrow abs" style="left:98px"><svg width="16" height="16" viewBox="0 0 16 16"><path d="M11 2 5 8l6 6" fill="none" stroke="#fff" stroke-width="2.5"/></svg></div>
<div class="gal-arrow abs" style="left:702px"><svg width="16" height="16" viewBox="0 0 16 16"><path d="M5 2l6 6-6 6" fill="none" stroke="#fff" stroke-width="2.5"/></svg></div>
<div class="gallery-side abs" role="img" aria-label="Modern terrace with lawn and mountain view" style="top:2401px;height:180px;background:linear-gradient(160deg,#8aa0b4,#c8c2b0 45%,#6a8a3a 80%)"></div>
<div class="gallery-side abs" role="img" aria-label="Bright white living room with large windows" style="top:2594px;height:175px;background:linear-gradient(160deg,#d8d4cc,#f2efe8 50%,#9a8c7a)"></div>

<footer class="footer abs">
  <div class="footer-brand abs">Lantern Dwelling Partners</div>
  <div class="footer-col abs" style="left:426px;width:200px">
    <h3>Contact Us</h3>
    <div class="contact-line"><svg width="14" height="14" viewBox="0 0 14 14"><path d="M3 1l2.5 3-1.5 1.5a8 8 0 0 0 4.5 4.5L10 8.5 13 11l-1.5 2C6 13 1 8 1 2.5z" fill="#fff"/></svg>(000)-555-0142 (Phone)</div>
    <div class="contact-line"><svg width="14" height="14" viewBox="0 0 14 14"><rect x="3" y="1" width="8" height="4" fill="#fff"/><rect x="1" y="5" width="12" height="6" rx="1" fill="#fff"/><rect x="3" y="9" width="8" height="4" fill="#2b2b2b" stroke="#fff"/></svg>(000)-555-0143 (Fax)</div>
    <div class="contact-line"><svg width="14" height="14" viewBox="0 0 14 14"><rect x="1" y="3" width="12" height="8" fill="#fff"/><path d="M1 3l6 5 6-5" fill="none" stroke="#2b2b2b"/></svg><u>info@lanterndwelling.example</u></div>
    <div class="contact-line"><svg width="14" height="14" viewBox="0 0 9 12"><path d="M4.5 0A4.5 4.5 0 0 0 0 4.5C0 8 4.5 12 4.5 12S9 8 9 4.5A4.5 4.5 0 0 0 4.5 0z" fill="#fff"/></svg>P.O Box 418 Harbor Lane<br>Suite 9</div>
  </div>
  <div class="footer-col abs" style="left:652px;width:220px">
    <h3>Newsletter</h3>
    <p style="font-size:12px;line-height:20px">Register Your email address to get information about us</p>
    <div class="email-input">Email Address</div>
    <div class="btn-sub">SUBSCRIBE</div>
  </div>
  <div class="footer-col abs" style="left:905px;width:210px">
    <h3>Follow Us</h3>
    <p style="font-size:11.5px;line-height:19px">Lorem ipsum dolor sit amet, conse ctetur adipiscing elit. Nulla in purus nibh. Donec ornare</p>
    <div class="social"><i></i><i></i><i></i><i></i><i></i></div>
  </div>
</footer>
<div class="copyright abs">© Copyright 2016 Lantern Dwelling Partners All Rights Reserved</div>

</body>
</html>
```